Financial Advisor Resource Firm needs business card design

Need business card design for company in Omaha NE called Meridale Circle. We provide resources to financial advisors....workshop programs, retirement analysis, and insurance planning. I would like to see designs that use grays, greens, black, and white colors. The final design should communicate 'collaboration' and be simple yet attractive to financial planning clients. I will attached our logo and another picture of a puzzle piece coming together. I would like the incorporate the puzzle picture somehow, maybe on the back somehow, with color or just the gray scale....OR, the picture be the front of the card with 'Meridale' definition on it (see upload) and then company logo, employee name, title, address on the back (see ppt uploaded). The following disclosure needs to be included somewhere- Advisory services offered through Stonebrook Assets, LLC.
Updates

I uploaded a svg and ai file of the logo

Target Market(s)

Financial planning clients and financial advisors....so pretty diverse age range of about 40-70.

Industry/Entity Type

Financial Planning

Contact Information for Business Card

Tobias L. Fenwright, MBA
Founder/President
5287 E. Larkin Road
Suite 230
Omaha, NE 68190
Phone- (402) 555-0147
Cell- (402) 555-0183
Fax- (402) 555-0129
email- tobias@meridaleplan.example
web address- www.meridaleplan.example

Colors
1b1b1b
474747
d3d3d3
ffffff
9bcb3c
abd036

Requirements
Must have
• Must include logo provided, must be 2 sided, and must have disclosure...all of these items listed in project description

```html
<!DOCTYPE html>
<html lang="en">
<head>
<meta charset="utf-8">
<title>Meridale Circle – Business Card</title>
<link href="https://fonts.googleapis.com/css2?family=Lato:wght@300;400;700&display=swap" rel="stylesheet">
<style>
  :root {
    --ink: #1b1b1b;
    --graphite: #474747;
    --silver: #d3d3d3;
    --white: #ffffff;
    --green: #9bcb3c;
    --green-bright: #abd036;
    --backdrop: #2a2a2a;
  }
  * { box-sizing: border-box; margin: 0; padding: 0; }
  html, body {
    width: 1200px; height: 900px; overflow: hidden;
    background: var(--backdrop);
    font-family: "Lato", Arial, sans-serif;
  }
  .stage {
    width: 1200px; height: 900px;
    display: flex; flex-direction: column; align-items: center; justify-content: center;
    gap: 48px;
  }
  .card {
    position: relative;
    width: 640px; height: 366px;
    border-radius: 22px;
    overflow: hidden;
    box-shadow: 0 10px 30px rgba(0,0,0,.45);
  }

  /* Back side */
  .card-back { background: var(--graphite); }
  .card-back .photo {
    position: absolute; inset: 0;
    background:
      radial-gradient(ellipse at 70% 40%, #9a9a9a 0%, #6e6e6e 35%, transparent 70%),
      linear-gradient(135deg, #8a8a8a 0%, #5c5c5c 45%, #3a3a3a 100%);
  }
  .card-back .shade {
    position: absolute; left: 0; right: 0; bottom: 0; height: 60%;
    background: linear-gradient(to bottom, rgba(40,40,40,0), rgba(40,40,40,.85));
  }
  .card-back .motto {
    position: absolute; left: 0; right: 0; top: 178px;
    text-align: center; color: var(--white);
    font-weight: 400; font-size: 19px; letter-spacing: .2px;
  }
  .card-back .rule {
    position: absolute; left: 48px; right: 48px; top: 282px;
    height: 1px; background: rgba(255,255,255,.45);
  }
  .card-back .disclosure {
    position: absolute; left: 0; right: 0; top: 300px;
    text-align: center; color: var(--white);
    font-weight: 400; font-size: 15px; letter-spacing: .6px; text-transform: uppercase;
  }

  /* Front side */
  .card-front {
    background: linear-gradient(160deg, #262626 0%, var(--ink) 60%);
    color: var(--white);
  }
  .brand {
    position: absolute; top: 58px; left: 0; right: 0;
    text-align: center;
    font-weight: 400; font-size: 46px; letter-spacing: 3px;
    text-transform: uppercase; color: var(--white);
  }
  .brand-rule {
    position: absolute; left: 40px; right: 40px; top: 156px;
    height: 1px; background: rgba(255,255,255,.18);
  }
  .person { position: absolute; left: 40px; top: 186px; }
  .person .name {
    font-weight: 700; font-size: 22px; color: var(--green);
    text-transform: uppercase; letter-spacing: .3px;
  }
  .person .name .cred { font-weight: 400; font-size: 16px; }
  .person .title { font-size: 18px; font-weight: 400; margin-top: 2px; }
  .contacts { list-style: none; margin-top: 14px; }
  .contacts li {
    display: flex; align-items: center; gap: 8px;
    font-size: 18px; line-height: 24px;
  }
  .contacts svg { width: 14px; height: 14px; fill: var(--green); flex: none; }
  .office {
    position: absolute; right: 40px; top: 186px;
    text-align: right; font-size: 18px; line-height: 24px;
  }
  .office .web { color: var(--green); margin-bottom: 8px; }
</style>
</head>
<body>
<main class="stage">

  <section class="card card-back" aria-label="Card back">
    <div class="photo" role="img" aria-label="Grayscale photograph of hands fitting two puzzle pieces together"></div>
    <div class="shade"></div>
    <p class="motto">To come together and unite in common interest and focus</p>
    <div class="rule"></div>
    <p class="disclosure">Advisory services offered through Stonebrook Assets, LLC.</p>
  </section>

  <section class="card card-front" aria-label="Card front">
    <h1 class="brand">Meridale Circle</h1>
    <div class="brand-rule"></div>

    <div class="person">
      <p class="name">Tobias L. Fenwright, <span class="cred">MBA</span></p>
      <p class="title">Founder/President</p>
      <ul class="contacts">
        <li>
          <svg viewBox="0 0 16 16" aria-hidden="true"><path d="M2 5c0-2 2-3 6-3s6 1 6 3v1h-3V5H5v1H2zM3 7h10l1 6H2zm5 1.5a2 2 0 1 0 0 4 2 2 0 0 0 0-4z"/></svg>
          (402) 555-0147
        </li>
        <li>
          <svg viewBox="0 0 16 16" aria-hidden="true"><path d="M4 1h8v14H4zm1.5 1.5v9h5v-9zM8 12.5a.8.8 0 1 0 0 1.6.8.8 0 0 0 0-1.6z" fill-rule="evenodd"/></svg>
          (402) 555-0183
        </li>
        <li>
          <svg viewBox="0 0 16 16" aria-hidden="true"><path d="M4 1h7l1 1v4H4zM1 7h14v6h-3v2H4v-2H1zm4 4v2.5h6V11z"/></svg>
          (402) 555-0129
        </li>
        <li>
          <svg viewBox="0 0 16 16" aria-hidden="true"><path d="M1 3h14v10H1zm1.5 1.5L8 9l5.5-4.5z"/></svg>
          tobias@meridaleplan.example
        </li>
      </ul>
    </div>

    <div class="office">
      <p class="web">www.meridaleplan.example</p>
      <p>5287 E. Larkin Road</p>
      <p>Suite 230 Omaha, NE 68190</p>
    </div>
  </section>

</main>
</body>
</html>
```